Equipment Finance Specialist I work with companies who need the funds to buy their equipment

I would like a business card that stands out on the shelves. I want to be able to hand it to someone and say WOW. This card should have my logo.
You can put color into it I am very open on design and color

What my company does is we deal with dealerships that sell equipment such as Dump Trucks garbage trucks tractors trailers. Customers get referred to us and depending on their time in business we will ask for the following items

Companies that have been in business for more than two years we have a credit application program up to 250K . With this program we need the following items Credit application filled out(which is what I would like to be able for the customer to click on my website to get.) as well as three current month bank statements.

Deals over 250k we will need the following items

2 years business tax returns
2 years personal tax returns
Profit & Loss statement
Personal Financial Statement

what we do
100% FINANCING
SEASONAL PAYMENTS
LOAN BALLOON PAYMENTS
TRAC LEASING
LOW-INTEREST REFINANCING RATES
DEBT CONSOLIDATION

We specialize in creative financing solutions and offer a variety of reliable, flexible and expandable lending choices.

Target Market(s)

Trucking Companies

Industry/Entity Type

Trucking Company

Contact Information for Business Card

* $250,000 Application only Program
* Loans from $30,000 to 5,000,000
* Competitive Interest Rates

Font styles to use
Serif
Sans Serif

Colors

Designer to choose colors to be used in the design.

Requirements
Must have
• On the back of the card.
• * $250,000 Application only Program
• * Loans from $30,000 to 5,000,000
• My name, email, website. address
• * Competitive Interest Rates
• * 100% Financing
Nice to have
• I want my logo to pop on the card
• My logo is the great one I would like to use
Should not have
• I am up for your creativity as well

```html
<!DOCTYPE html>
<html lang="en">
<head>
<meta charset="utf-8">
<title>Summit Lending – Business Card</title>
<link rel="stylesheet" href="https://fonts.googleapis.com/css2?family=Open+Sans:wght@400;600;800&display=swap">
<style>
  :root {
    --navy: #1c2f78;
    --navy-soft: #4a5ea8;
    --red: #d0173a;
    --grey: #5b5b5b;
    --paper: #ffffff;
    --stage: #2b2b2d;
  }
  * { margin: 0; padding: 0; box-sizing: border-box; }
  html, body { width: 1200px; height: 892px; overflow: hidden; }
  body {
    background: var(--stage);
    font-family: "Open Sans", Arial, sans-serif;
    position: relative;
  }
  .card {
    position: absolute;
    width: 600px;
    height: 343px;
    background: var(--paper);
    box-shadow: 0 10px 30px rgba(0,0,0,.45);
    overflow: hidden;
  }
  .card--back { left: 90px; top: 70px; }
  .card--front { left: 510px; top: 470px; }

  .brand {
    display: flex;
    align-items: center;
    gap: 16px;
  }
  .brand__mark {
    width: 96px; height: 96px;
    border-radius: 50%;
    background: radial-gradient(circle at 42% 38%, var(--navy-soft) 0%, var(--navy) 72%);
  }
  .brand__text { display: flex; flex-direction: column; }
  .brand__name {
    font-weight: 800;
    color: var(--navy);
    font-size: 40px;
    line-height: .95;
    letter-spacing: .5px;
    text-transform: uppercase;
  }
  .brand__rule {
    display: block;
    margin-top: 8px;
    height: 6px;
    width: 100%;
    background: var(--red);
  }

  .card--back .brand {
    position: absolute;
    left: 0; right: 0; top: 72px;
    justify-content: center;
  }
  .offer {
    position: absolute;
    left: 0; right: 0; top: 228px;
    text-align: center;
    color: var(--grey);
    font-size: 15px;
    line-height: 1.45;
  }

  .card--front .brand { position: absolute; left: 46px; top: 40px; }
  .card--front .brand__name { font-size: 34px; }
  .card--front .brand__rule { height: 5px; margin-top: 6px; }
  .person {
    position: absolute;
    left: 46px; top: 140px;
  }
  .person__accent {
    position: absolute;
    left: -46px; top: 2px;
    width: 14px; height: 38px;
    background: var(--navy);
  }
  .person__name {
    font-weight: 800;
    color: var(--navy);
    font-size: 20px;
    text-transform: uppercase;
    line-height: 1.1;
  }
  .person__title {
    color: var(--red);
    font-size: 15px;
    text-transform: uppercase;
  }
  .contact {
    position: absolute;
    left: 46px; top: 212px;
    color: var(--grey);
    font-size: 14.5px;
    line-height: 1.4;
    font-style: normal;
  }
  .contact__gap { margin-top: 10px; }
  .contact__label { color: var(--navy); font-weight: 800; }
  .emblem-area {
    position: absolute;
    right: 34px; top: 36px;
    width: 272px; height: 272px;
    border-radius: 50%;
    background: radial-gradient(circle at 42% 38%, var(--navy-soft) 0%, var(--navy) 72%);
  }
</style>
</head>
<body>
  <section class="card card--back" aria-label="Business card back">
    <div class="brand">
      <span class="brand__mark" role="img" aria-label="Brand emblem area: navy circle where the company mark sits"></span>
      <span class="brand__text">
        <span class="brand__name">Summit<br>Lending</span>
        <span class="brand__rule"></span>
      </span>
    </div>
    <p class="offer">
      $250,000 Application only Program • Loans from $30,000 to 5,000,000<br>
      Competitive Interest Rates • 100% Financing
    </p>
  </section>

  <section class="card card--front" aria-label="Business card front">
    <div class="brand">
      <span class="brand__text">
        <span class="brand__name">Summit<br>Lending</span>
        <span class="brand__rule"></span>
      </span>
    </div>
    <div class="person">
      <span class="person__accent"></span>
      <p class="person__name">Mark Halden</p>
      <p class="person__title">President</p>
    </div>
    <address class="contact">
      <p>4120 Harbor Lane</p>
      <p>Glen Falls, NY 12801</p>
      <p class="contact__gap"><span class="contact__label">P:</span> 555 0142 7788</p>
      <p>mark@summitlending.com</p>
      <p>www.summitlending.com</p>
    </address>
    <div class="emblem-area" role="img" aria-label="Large brand emblem area: navy circle where the company mark sits"></div>
  </section>
</body>
</html>
```